New Business Card Design Project

Need a design that will create an impact / strong impression towards our clients for our business. We are in the lighting business and we do lighting retrofits for large commercial to industrial clientele.

Target Market(s)

Lighting Industry

Industry/Entity Type

Business

Font styles to use
Other font styles liked:
• we would like to use the font on our logo, not sure what it is though..

Requirements
Must have
• Our logo.
Nice to have
• We are open to suggestions that have to do with lighting.

```html
<!DOCTYPE html>
<html lang="en">
<head>
<meta charset="utf-8">
<title>Lumora Retrofit Group – Business Card</title>
<link href="https://fonts.googleapis.com/css2?family=Montserrat:wght@400;500;600&family=Oswald:wght@500&display=swap" rel="stylesheet">
<style>
  :root {
    --backdrop: #151515;
    --card: #262626;
    --card-edge: #2e2e2e;
    --green: #2a9d48;
    --green-light: #4cc25f;
    --white: #f2f2f2;
    --grey: #8a8a8a;
    --logo-grey: #bdbdbd;
  }
  * { margin: 0; padding: 0; box-sizing: border-box; }
  html, body {
    width: 1200px; height: 900px; overflow: hidden;
    background: var(--backdrop);
    font-family: "Montserrat", sans-serif;
  }
  .canvas {
    position: relative; width: 1200px; height: 900px;
    display: flex; flex-direction: column; align-items: center; justify-content: center; gap: 36px;
  }
  .card {
    position: relative; width: 700px; height: 400px;
    background: linear-gradient(160deg, var(--card) 0%, #2a2a2a 60%, var(--card-edge) 100%);
    box-shadow: 0 10px 30px rgba(0,0,0,.55);
  }
  /* Front */
  .card-front { display: flex; flex-direction: column; align-items: center; justify-content: center; }
  .brand { display: flex; align-items: center; gap: 14px; }
  .brand-mark { width: 22px; height: 22px; background: var(--logo-grey); }
  .brand-name {
    font-weight: 600; font-size: 30px; letter-spacing: 2px;
    color: var(--logo-grey); text-transform: uppercase;
  }
  .front-web {
    position: absolute; bottom: 62px; left: 0; right: 0; text-align: center;
    font-size: 13px; letter-spacing: 2px; color: #6e6e6e;
  }
  /* Back */
  .identity {
    position: absolute; left: 150px; top: 150px; width: 230px; text-align: right;
  }
  .person-name {
    font-family: "Oswald", sans-serif; font-weight: 500;
    font-size: 40px; line-height: 1; color: var(--green);
    text-transform: uppercase; letter-spacing: .5px;
  }
  .person-title { font-size: 20px; color: var(--grey); margin-top: 4px; }
  .divider {
    position: absolute; left: 405px; top: 152px; width: 2px; height: 80px;
    background: var(--green);
  }
  .contacts { position: absolute; left: 432px; top: 160px; list-style: none; }
  .contacts li {
    display: flex; align-items: center; gap: 14px;
    font-size: 17px; color: var(--white); letter-spacing: .8px; height: 26px;
  }
  .contacts svg { width: 14px; height: 14px; fill: var(--green); flex: none; }
  .location {
    position: absolute; left: 120px; bottom: 62px;
    font-size: 18px; color: var(--white); letter-spacing: .8px;
  }
  .location-label { color: var(--green-light); }
</style>
</head>
<body>
<main class="canvas">
  <section class="card card-front" aria-label="Card front">
    <div class="brand">
      <span class="brand-mark"></span>
      <span class="brand-name">Lumora Retrofit Group, LLC</span>
    </div>
    <p class="front-web">www.lumoragroup.com</p>
  </section>

  <section class="card card-back" aria-label="Card back">
    <div class="identity">
      <h1 class="person-name">Daniel Reyes</h1>
      <p class="person-title">Founder</p>
    </div>
    <span class="divider"></span>
    <ul class="contacts">
      <li>
        <svg viewBox="0 0 24 24" aria-hidden="true"><path d="M6.6 10.8a15.1 15.1 0 0 0 6.6 6.6l2.2-2.2a1 1 0 0 1 1-.25 11.4 11.4 0 0 0 3.6.57 1 1 0 0 1 1 1V20a1 1 0 0 1-1 1A17 17 0 0 1 3 4a1 1 0 0 1 1-1h3.5a1 1 0 0 1 1 1c0 1.25.2 2.45.57 3.57a1 1 0 0 1-.25 1z"/></svg>
        0400 555 019
      </li>
      <li>
        <svg viewBox="0 0 24 24" aria-hidden="true"><path d="M2 5h20v14H2z" opacity=".0"/><path d="M2 5h20v2l-10 6L2 7zM2 9l10 6 10-6v10H2z"/></svg>
        info@lumoragroup.com
      </li>
      <li>
        <svg viewBox="0 0 24 24" aria-hidden="true"><path d="M12 2a10 10 0 1 0 0 20 10 10 0 0 0 0-20zm6.9 6h-2.9a15 15 0 0 0-1.4-3.6A8 8 0 0 1 18.9 8zM12 4c.8 1.2 1.5 2.5 1.9 4h-3.8c.4-1.5 1.1-2.8 1.9-4zM4.3 14a8 8 0 0 1 0-4h3.4a16 16 0 0 0 0 4zm.8 2h2.9c.3 1.3.8 2.5 1.4 3.6A8 8 0 0 1 5.1 16zM8 8H5.1a8 8 0 0 1 4.3-3.6C8.8 5.5 8.3 6.7 8 8zm4 12c-.8-1.2-1.5-2.5-1.9-4h3.8c-.4 1.5-1.1 2.8-1.9 4zm2.3-6H9.7a14 14 0 0 1 0-4h4.6a14 14 0 0 1 0 4zm.3 5.6c.6-1.1 1.1-2.3 1.4-3.6h2.9a8 8 0 0 1-4.3 3.6zM16.3 14a16 16 0 0 0 0-4h3.4a8 8 0 0 1 0 4z"/></svg>
        www.lumoragroup.com
      </li>
    </ul>
    <p class="location"><span class="location-label">Location:</span> 4820 Canyon Road, Suite Tucson 85700</p>
  </section>
</main>
</body>
</html>
```